Elegant One-Page Flyer That Catches People's Eye

For a series of workshops and zoom calls I am marketing with a colleague of mine, we would like to have an elegant, catchy one-page flyer that entices people to contact us. I am envisioning a one-page flyer (a card that is somewhat larger than a postcard) with great text, layout and images which magnetically draws people to us and is positive and inspiring. Also, if at all possible, a QR code linking it to our websites. Good colours would be shades of blue and green. I am uploading: the Text, our pictures, logos and contact information.

```html
<!DOCTYPE html>
<html lang="en">
<head>
<meta charset="utf-8">
<title>Rising Above Hidden Career Deal Breakers</title>
<link rel="stylesheet" href="https://fonts.googleapis.com/css2?family=Bebas+Neue&family=Poppins:wght@400;500;600;700;800&display=swap">
<style>
  :root {
    --green: #8fad62;
    --green-dark: #7a9650;
    --ink: #1c1c1c;
    --panel: #0b0a0a;
    --page: #1d1d1d;
    --white: #ffffff;
    --soft: #e9e9e9;
  }
  * { box-sizing: border-box; margin: 0; padding: 0; }
  html, body { width: 785px; height: 1200px; overflow: hidden; background: var(--page); }
  body { font-family: "Poppins", sans-serif; color: var(--white); }
  .flyer { position: relative; width: 785px; height: 1200px; background: var(--page); overflow: hidden; }

  .hero-photo {
    position: absolute; left: 0; top: 0; width: 785px; height: 680px;
    background:
      radial-gradient(ellipse 260px 200px at 420px 330px, rgba(214,150,92,.75), transparent 70%),
      radial-gradient(ellipse 200px 330px at 560px 250px, rgba(60,45,40,.85), transparent 75%),
      radial-gradient(ellipse 180px 420px at 730px 330px, rgba(120,85,62,.8), transparent 75%),
      linear-gradient(180deg, #6e7379 0%, #8a8580 28%, #a98264 47%, #4e3e35 68%, var(--page) 100%);
  }

  .intro { position: absolute; left: 54px; top: 48px; width: 400px; }
  .intro-question { font-weight: 800; font-size: 24px; line-height: 1.0; text-transform: uppercase; }
  .intro-lead { margin-top: 8px; font-size: 16px; line-height: 1.12; color: var(--soft); }

  .title { position: absolute; left: 54px; top: 194px; font-family: "Bebas Neue", sans-serif; font-size: 54px; line-height: .82; font-weight: 400; }
  .title .dark { color: #1b1b1b; display: block; }
  .title .light { color: var(--white); display: block; }

  .format-pill { position: absolute; left: 54px; top: 289px; width: 684px; height: 62px; border-radius: 31px; background: var(--white); overflow: hidden; display: flex; align-items: center; }
  .format-pill .workshops { width: 320px; height: 100%; background: var(--green); font-family: "Bebas Neue", sans-serif; font-size: 48px; line-height: 64px; padding-left: 12px; color: var(--white); }
  .format-pill .plus { position: absolute; left: 306px; top: 12px; font-weight: 800; font-size: 30px; color: var(--ink); line-height: 36px; }
  .format-pill .sessions { margin-left: 33px; font-weight: 700; font-size: 15px; line-height: 1.2; color: var(--ink); }

  .breakers-lead { position: absolute; left: 55px; top: 365px; font-weight: 700; font-size: 17px; line-height: 1.2; }
  .breakers-lead em { font-style: normal; color: var(--green); }
  .breakers-box { position: absolute; left: 55px; top: 398px; width: 676px; height: 114px; border: 1.5px dashed var(--green); border-top: none; border-radius: 0 0 8px 8px; }
  .breakers-box::before { content: ""; position: absolute; top: 0; left: 0; width: 6px; border-top: 1.5px dashed var(--green); }
  .breakers-box::after { content: ""; position: absolute; top: 0; right: 0; width: 222px; border-top: 1.5px dashed var(--green); }
  .breakers-dot { position: absolute; left: 505px; top: 395px; width: 6px; height: 6px; border-radius: 50%; background: var(--green); }
  .breaker { position: absolute; display: flex; gap: 10px; font-size: 15px; line-height: 1.2; color: var(--soft); }
  .breaker svg { flex: none; margin-top: 2px; }

  .section-label { position: absolute; left: 0; width: 785px; top: 528px; text-align: center; font-weight: 600; font-size: 22px; letter-spacing: 4px; }

  .facilitator { position: absolute; left: 78px; width: 648px; height: 166px; border: 2px solid var(--green); border-radius: 83px; background: var(--panel); }
  .portrait { position: absolute; left: 7px; top: 6px; width: 150px; height: 150px; border-radius: 50%; background: radial-gradient(circle at 50% 45%, #d9cfc8, #f3f1ef 70%); }
  .facilitator-text { position: absolute; left: 212px; top: 18px; width: 390px; }
  .facilitator-name { font-weight: 700; font-size: 22px; line-height: 1.2; color: var(--green); }
  .facilitator-bio { margin-top: 5px; font-size: 15px; line-height: 1.18; color: var(--soft); }

  .brand { position: absolute; display: flex; align-items: center; gap: 12px; }
  .brand-quill { left: 92px; top: 958px; color: var(--green); font-size: 34px; font-weight: 400; }
  .brand-quill .mark { width: 44px; height: 44px; border-radius: 50%; border: 2px solid var(--green); }
  .brand-korbach { left: 432px; top: 962px; color: var(--white); font-size: 28px; font-weight: 500; }

  .contact-panel { position: absolute; left: 43px; top: 1044px; width: 698px; height: 126px; background: #0d0d0d; border-radius: 14px; }
  .contact-tab { position: absolute; left: 129px; top: -8px; width: 434px; height: 43px; background: var(--green-dark); border-radius: 0 0 26px 26px; text-align: center; font-weight: 700; font-size: 15px; line-height: 1.2; padding-top: 2px; }
  .contact-tab::before, .contact-tab::after { content: ""; position: absolute; top: 0; width: 30px; height: 8px; background: var(--green-dark); }
  .contact-tab::before { left: -26px; border-radius: 8px 0 0 0; }
  .contact-tab::after { right: -26px; border-radius: 0 8px 0 0; }
  .contact-divider { position: absolute; left: 301px; top: 52px; height: 56px; border-left: 1.5px dashed var(--green); }
  .contact { position: absolute; top: 54px; }
  .contact-name { font-weight: 700; font-size: 13px; color: var(--green); text-transform: uppercase; }
  .contact-line { display: flex; align-items: center; gap: 8px; font-weight: 600; font-size: 15px; line-height: 1.3; }
</style>
</head>
<body>
<main class="flyer">
  <div class="hero-photo" role="img" aria-label="Photo of a climber with a backpack scaling a rock face at sunset"></div>

  <header class="intro">
    <h1 class="intro-question">Is your career going<br>the way you want?</h1>
    <p class="intro-lead">If not, do you feel stuck? Blocked?<br>Frustrated? Don’t know what to do<br>about this?</p>
  </header>

  <h2 class="title"><span class="dark">Rising above hidden</span><span class="light">Career deal breakers</span></h2>

  <div class="format-pill">
    <div class="workshops">4 Mini-Workshops</div>
    <span class="plus">+</span>
    <p class="sessions">2 short Online Group Coaching<br>Sessions between Workshops</p>
  </div>

  <p class="breakers-lead">Learn to overcome and rise above<br>the <em>4 top hidden career deal breakers fast</em></p>
  <span class="breakers-dot"></span>
  <div class="breakers-box"></div>

  <div class="breaker" style="left:72px;top:419px">
    <svg width="14" height="14" viewBox="0 0 14 14"><circle cx="7" cy="7" r="6" fill="none" stroke="#8fad62" stroke-width="1.2"/><path d="M4 7.2l2 2 4-4.4" fill="none" stroke="#8fad62" stroke-width="1.4"/></svg>
    <span>Microaggressions</span>
  </div>
  <div class="breaker" style="left:72px;top:452px">
    <svg width="14" height="14" viewBox="0 0 14 14"><circle cx="7" cy="7" r="6" fill="none" stroke="#8fad62" stroke-width="1.2"/><path d="M4 7.2l2 2 4-4.4" fill="none" stroke="#8fad62" stroke-width="1.4"/></svg>
    <span>Workplace snakes and<br>other dysfunctional types</span>
  </div>
  <div class="breaker" style="left:372px;top:422px">
    <svg width="14" height="14" viewBox="0 0 14 14"><circle cx="7" cy="7" r="6" fill="none" stroke="#8fad62" stroke-width="1.2"/><path d="M4 7.2l2 2 4-4.4" fill="none" stroke="#8fad62" stroke-width="1.4"/></svg>
    <span>Toxic black box team dynamics</span>
  </div>
  <div class="breaker" style="left:372px;top:455px">
    <svg width="14" height="14" viewBox="0 0 14 14"><circle cx="7" cy="7" r="6" fill="none" stroke="#8fad62" stroke-width="1.2"/><path d="M4 7.2l2 2 4-4.4" fill="none" stroke="#8fad62" stroke-width="1.4"/></svg>
    <span>Disempowering Subconscious<br>Algorithms</span>
  </div>

  <h3 class="section-label">FACILITATORS</h3>

  <article class="facilitator" style="top:565px">
    <div class="portrait" role="img" aria-label="Portrait photo of Dr. Mara Vennick"></div>
    <div class="facilitator-text">
      <h4 class="facilitator-name">Dr. Mara Vennick</h4>
      <p class="facilitator-bio">PhD, CPC, is an American &amp; Swiss-Trained<br>Work &amp; Organizational Psychologist,<br>ICF-Certified Coach, Board Certified<br>Hypnotherapist, Certified Naturopath (TEN)<br>&amp; Certified Ayurvedic Practitioner.</p>
    </div>
  </article>

  <article class="facilitator" style="top:750px">
    <div class="portrait" role="img" aria-label="Portrait photo of Dr. Helena Korbach"></div>
    <div class="facilitator-text" style="top:24px">
      <h4 class="facilitator-name">Dr. Helena Korbach</h4>
      <p class="facilitator-bio">Ph.D., PCC is a coach and somatic<br>experience practitioner, a team coach<br>with diploma and a certified virtual<br>team coach.</p>
    </div>
  </article>

  <div class="brand brand-quill"><span class="mark"></span><span>Quillbrook Vale</span></div>
  <div class="brand brand-korbach"><span>Korbach Coaching</span></div>

  <section class="contact-panel">
    <div class="contact-tab">For dates, venue and further information<br>Contact Helena or Mara at</div>
    <div class="contact" style="left:72px">
      <p class="contact-name">Dr. Mara Vennick</p>
      <p class="contact-line"><svg width="12" height="12" viewBox="0 0 12 12"><path d="M2.5 1l2 2.5-1 1.2c.7 1.4 1.6 2.3 2.8 2.8l1.2-1L10 8.5 8.8 10.6C5 10 2 7 1.4 3.2z" fill="#8fad62"/></svg>076 204 5813</p>
      <p class="contact-line"><svg width="13" height="10" viewBox="0 0 13 10"><rect x=".5" y=".5" width="12" height="9" fill="#8fad62"/><path d="M.5 .8l6 4.6 6-4.6" fill="none" stroke="#0d0d0d" stroke-width="1"/></svg>mara@quillbrookvale.ch</p>
    </div>
    <div class="contact-divider"></div>
    <div class="contact" style="left:359px">
      <p class="contact-name">Dr. Helena Korbach</p>
      <p class="contact-line"><svg width="12" height="12" viewBox="0 0 12 12"><path d="M2.5 1l2 2.5-1 1.2c.7 1.4 1.6 2.3 2.8 2.8l1.2-1L10 8.5 8.8 10.6C5 10 2 7 1.4 3.2z" fill="#8fad62"/></svg>079 612 38 90</p>
      <p class="contact-line"><svg width="13" height="10" viewBox="0 0 13 10"><rect x=".5" y=".5" width="12" height="9" fill="#8fad62"/><path d="M.5 .8l6 4.6 6-4.6" fill="none" stroke="#0d0d0d" stroke-width="1"/></svg>helena@korbachcoaching.ch</p>
    </div>
  </section>
</main>
</body>
</html>
```